ambitious event and festival agency from austria needs fresh business card design

A new design is due for the new headquarters and the new challenges. We organize events for different target groups from 16 to 60 years. The design should therefore be straightforward and not confused, so we are open to new colors and the logo may also be changed. In general, however, the most interesting suggestions are the most interesting ones. after this order we are looking for more graphics for brightloom facebook instagramm homepage etc A new design is due for the new headquarters and the new challenges. We organize events for different target groups from 16 to 60 years. The design should therefore be straightforward and not confused, so we are open to new colors and the logo may also be changed. In general, however, the most interesting suggestions are the most interesting ones. after this order we are looking for more graphics for brightloom facebook instagramm homepage etc A new design is due for the new headquarters and the new challenges. We organize events for different target groups from 16 to 60 years. The design should therefore be straightforward and not confused, so we are open to new colors and the logo may also be changed. In general, however, the most interesting suggestions are the most interesting ones. after this order we are looking for more graphics for brightloom facebook instagramm homepage etc
Updates

Reason: I am sorry for this decision but i need some more time. No new designs please, there are so many good ones and I will have made a decision in the next 3 days.

Target Market(s)

Industry/Entity Type

Business

Font styles to use
Serif
Sans Serif

Colors

Designer to choose colors to be used in the design.

Requirements
Must have
Nice to have
Should not have

```html
<!DOCTYPE html>
<html lang="en">
<head>
<meta charset="utf-8">
<title>brightloom business card</title>
<link href="https://fonts.googleapis.com/css2?family=Work+Sans:wght@400;500;600&family=Oswald:wght@500&display=swap" rel="stylesheet">
<style>
  :root {
    --stage: #2b2b2d;
    --card-light: #3a3a3c;
    --card-dark: #050505;
    --brand-red: #c4354c;
    --panel-red: #5a2a30;
    --text-light: #f2f2f2;
    --text-muted: #8a8a8a;
  }
  * { box-sizing: border-box; margin: 0; padding: 0; }
  html, body { width: 1200px; height: 900px; overflow: hidden; background: var(--stage); }
  body { position: relative; font-family: "Work Sans", sans-serif; }

  .card {
    position: absolute;
    left: 290px;
    width: 620px;
    height: 390px;
    border-radius: 22px;
    overflow: hidden;
    background: linear-gradient(100deg, var(--card-light) 0%, #1b1b1c 45%, var(--card-dark) 72%);
    box-shadow: 0 18px 40px rgba(0,0,0,.55);
  }
  .card--front { top: 40px; }
  .card--back { top: 470px; }

  .wordmark {
    font-family: "Work Sans", sans-serif;
    font-weight: 600;
    color: var(--brand-red);
    letter-spacing: 0.5px;
    line-height: 1;
  }
  .card--front .wordmark {
    position: absolute;
    left: 0; right: 0; top: 160px;
    text-align: center;
    font-size: 64px;
  }

  .accent-panel {
    position: absolute;
    left: 0; top: 0;
    width: 330px; height: 100%;
    background: linear-gradient(120deg, rgba(120,52,60,.55) 0%, rgba(70,32,38,.35) 60%, rgba(70,32,38,0) 100%);
  }

  .pointer { position: absolute; left: 34px; top: 128px; }

  .holder { position: absolute; left: 64px; top: 120px; }
  .holder__name {
    font-family: "Oswald", sans-serif;
    font-weight: 500;
    font-style: italic;
    font-size: 26px;
    color: var(--brand-red);
    text-transform: uppercase;
    letter-spacing: 0.5px;
  }
  .holder__role { font-size: 17px; color: var(--text-muted); margin-top: 0; }

  .card--back .wordmark {
    position: absolute;
    left: 346px; top: 58px;
    font-size: 46px;
  }

  .office { position: absolute; left: 346px; top: 140px; font-size: 17px; line-height: 1.35; color: var(--text-light); letter-spacing: 0.6px; }
  .office__name { color: var(--brand-red); }

  .contacts { position: absolute; left: 328px; top: 240px; list-style: none; font-size: 17px; color: var(--text-light); letter-spacing: 0.6px; }
  .contacts li { display: flex; align-items: center; gap: 12px; line-height: 1.6; }
  .contacts svg { width: 13px; height: 13px; flex: none; }
  .contacts .hl { color: var(--brand-red); }
</style>
</head>
<body>

<section class="card card--front" aria-label="Card front">
  <div class="wordmark">brightloom</div>
</section>

<section class="card card--back" aria-label="Card back">
  <div class="accent-panel" role="img" aria-label="Soft red accent area behind the name"></div>

  <svg class="pointer" width="24" height="28" viewBox="0 0 24 28" aria-hidden="true">
    <polygon points="0,0 24,14 0,28" fill="#ffffff"/>
  </svg>

  <div class="holder">
    <div class="holder__name">Markus Feldinger</div>
    <div class="holder__role">Manager</div>
  </div>

  <div class="wordmark">brightloom</div>

  <address class="office" style="font-style:normal">
    <div class="office__name">brightloom</div>
    <div>Lindengasse 12</div>
    <div>A4020 Linz</div>
  </address>

  <ul class="contacts">
    <li>
      <svg viewBox="0 0 12 12" aria-hidden="true"><rect x="3" y="1" width="6" height="10" rx="1" fill="none" stroke="#c4354c" stroke-width="1.2"/><line x1="5" y1="9.3" x2="7" y2="9.3" stroke="#c4354c"/></svg>
      <span>+ 43 660 417 203 5</span>
    </li>
    <li>
      <svg viewBox="0 0 12 12" aria-hidden="true"><rect x="1" y="3" width="10" height="6.5" fill="none" stroke="#c4354c" stroke-width="1.2"/><polyline points="1,3 6,7 11,3" fill="none" stroke="#c4354c" stroke-width="1.2"/></svg>
      <span>m.feldinger@brightloom.eu</span>
    </li>
    <li>
      <svg viewBox="0 0 12 12" aria-hidden="true"><circle cx="6" cy="6" r="4.8" fill="none" stroke="#c4354c" stroke-width="1.1"/><ellipse cx="6" cy="6" rx="2" ry="4.8" fill="none" stroke="#c4354c" stroke-width="1"/><line x1="1.2" y1="6" x2="10.8" y2="6" stroke="#c4354c" stroke-width="1"/></svg>
      <span>www.<span class="hl">brightloom</span>.eu</span>
    </li>
  </ul>
</section>

</body>
</html>
```